Verlindo Magician

I want the business card for my business to give to people who watch that later I will be employed to show magic here is my website http://www.balsamomagicien.com/I want the interesting design , i am very opened for formal and informal, I watch a lot of design so don't stick to the common shape and form but i hope it can also be produced the thing to write on will be the same as in picture that i will upload , i also will upload the logo for you that so can be easy to useDenis CostilleMagicianMAGICIAN BALSAMO 17 rue des Tilleuls - 25000 BESANÇON contact@verlindoillusions.example tel. 0381 946 157 tel. 0674 219 503

```html
<!DOCTYPE html>
<html lang="fr">
<head>
<meta charset="utf-8">
<title>Verlindo Magician – Business Card</title>
<link href="https://fonts.googleapis.com/css2?family=Montserrat:wght@400;500&display=swap" rel="stylesheet">
<style>
  :root {
    --backdrop: #2b2d31;
    --card-white: #ffffff;
    --card-black: #0b0b0c;
    --ink: #161616;
    --ink-soft: #7a7a7a;
    --figure-dark: #1a1a1a;
    --figure-light: #5a5a5a;
  }
  * { box-sizing: border-box; margin: 0; padding: 0; }
  html, body {
    width: 1200px; height: 900px; overflow: hidden;
    background: var(--backdrop);
    font-family: "Montserrat", sans-serif;
  }
  .stage {
    width: 1200px; height: 900px;
    display: flex; flex-direction: column;
    align-items: center; justify-content: center; gap: 56px;
  }
  .card {
    width: 640px; height: 366px;
    border-radius: 26px;
    position: relative;
    box-shadow: 0 18px 40px rgba(0,0,0,.35);
  }
  /* front */
  .card--front { background: var(--card-white); color: var(--ink); }
  .brand {
    position: absolute; left: 40px; top: 30px;
    width: 150px; text-align: center;
  }
  .brand__figure {
    width: 120px; height: 104px; margin: 0 auto;
    border-radius: 40px 40px 8px 8px;
    background: linear-gradient(160deg, var(--figure-light), var(--figure-dark) 60%);
  }
  .brand__name {
    margin-top: 6px;
    font-size: 19px; font-weight: 400; letter-spacing: 1.5px;
    color: var(--ink);
  }
  .identity {
    position: absolute; right: 40px; top: 118px; text-align: right;
  }
  .identity__name {
    font-size: 30px; font-weight: 500; letter-spacing: 1px; line-height: 1;
  }
  .identity__role {
    margin-top: 6px;
    font-size: 15px; letter-spacing: 1.5px; color: var(--ink-soft);
  }
  .address {
    position: absolute; right: 40px; top: 196px;
    display: flex; align-items: center; gap: 14px;
  }
  .address__text {
    font-size: 17px; line-height: 1.2; letter-spacing: .5px;
  }
  .contacts {
    position: absolute; right: 40px; bottom: 28px;
    list-style: none; text-align: right;
  }
  .contacts li {
    display: flex; justify-content: flex-end; align-items: center; gap: 10px;
    font-size: 12px; letter-spacing: .8px; line-height: 22px; color: var(--ink);
  }
  .icon { width: 16px; height: 16px; flex: none; }
  .icon--pin { width: 26px; height: 32px; }
  /* back */
  .card--back { background: var(--card-black); display: flex; align-items: center; justify-content: center; }
  .emblem {
    width: 210px; height: 210px; border-radius: 50%;
    background: var(--card-white);
    display: flex; flex-direction: column; align-items: center; justify-content: center;
  }
  .emblem__figure {
    width: 100px; height: 96px;
    border-radius: 38px 38px 8px 8px;
    background: linear-gradient(160deg, var(--figure-light), var(--figure-dark) 60%);
  }
  .emblem__name {
    margin-top: 8px;
    font-size: 20px; letter-spacing: 1.5px; color: var(--ink);
  }
</style>
</head>
<body>
<main class="stage">
  <section class="card card--front">
    <div class="brand">
      <div class="brand__figure" role="img" aria-label="Black and white illustration of the magician holding playing cards"></div>
      <p class="brand__name">VERLINDO</p>
    </div>

    <div class="identity">
      <h1 class="identity__name">MARC RAVOULET</h1>
      <p class="identity__role">MAGICIAN</p>
    </div>

    <div class="address">
      <svg class="icon icon--pin" viewBox="0 0 26 32" aria-hidden="true">
        <path d="M13 1a9 9 0 0 0-9 9c0 7 9 15 9 15s9-8 9-15a9 9 0 0 0-9-9z" fill="#161616"/>
        <circle cx="13" cy="10" r="3.5" fill="#fff"/>
        <ellipse cx="13" cy="29" rx="9" ry="2.2" fill="none" stroke="#161616" stroke-width="1.6"/>
      </svg>
      <p class="address__text">17 RUE DES TILLEULS<br>25000 BESANÇON</p>
    </div>

    <ul class="contacts">
      <li>CONTACT@VERLINDOILLUSIONS.EXAMPLE
        <svg class="icon" viewBox="0 0 16 16" aria-hidden="true"><rect x="1" y="3" width="14" height="10" rx="1" fill="#161616"/><path d="M1.5 3.5 8 9l6.5-5.5" fill="none" stroke="#fff" stroke-width="1.3"/></svg>
      </li>
      <li>0381 946 157/0674 219 503
        <svg class="icon" viewBox="0 0 16 16" aria-hidden="true"><path d="M4 1.5 6.2 4 5 5.8c.9 2 2.3 3.4 4.2 4.2L11 8.8l2.5 2.2-1.3 2.7C6.6 13.4 2.6 9.4 2.3 3z" fill="#161616"/></svg>
      </li>
      <li>WWW.VERLINDOILLUSIONS.EXAMPLE
        <svg class="icon" viewBox="0 0 16 16" aria-hidden="true"><circle cx="8" cy="8" r="7" fill="#161616"/><path d="M1 8h14M8 1c-3 3.5-3 10.5 0 14M8 1c3 3.5 3 10.5 0 14M2.5 4.5h11M2.5 11.5h11" fill="none" stroke="#fff" stroke-width=".9"/></svg>
      </li>
    </ul>
  </section>

  <section class="card card--back">
    <div class="emblem">
      <div class="emblem__figure" role="img" aria-label="Black and white illustration of the magician holding playing cards"></div>
      <p class="emblem__name">VERLINDO</p>
    </div>
  </section>
</main>
</body>
</html>
```